wealth management firm, professional group, new model

we have a logo that works but we need a card, white background using our colors...clean look

our tag line if can be used in

Clear Plans for Every Tomorrow

```html
<!DOCTYPE html>
<html lang="en">
<head>
<meta charset="utf-8">
<title>Arvale Wealth Partners – Business Card</title>
<link rel="stylesheet" href="https://fonts.googleapis.com/css2?family=Montserrat:wght@400;500&display=swap">
<style>
  :root {
    --backdrop: #2b2b2b;
    --navy: #172b4d;
    --navy-deep: #14264a;
    --navy-ink: #1b2a48;
    --wave: #1e3258;
    --brand-mute: #4c5f80;
    --paper: #f1f1f1;
    --paper-shade: #e2e2e2;
    --white: #ffffff;
  }
  * { margin: 0; padding: 0; box-sizing: border-box; }
  html, body { width: 1200px; height: 576px; overflow: hidden; }
  body {
    background: var(--backdrop);
    font-family: "Montserrat", Arial, sans-serif;
    position: relative;
  }
  .card {
    position: absolute;
    top: 138px;
    width: 484px;
    height: 293px;
    border-radius: 9px;
    overflow: hidden;
  }
  /* Back side */
  .card--back {
    left: 102px;
    background: var(--navy-deep);
    display: flex;
    flex-direction: column;
    align-items: center;
    padding-top: 132px;
    color: var(--brand-mute);
    font-weight: 500;
  }
  .card--back .brand-name {
    font-size: 44px;
    letter-spacing: 0.5em;
    margin-right: -0.5em;
    line-height: 1;
  }
  .card--back .brand-line {
    margin-top: 22px;
    font-size: 16px;
    letter-spacing: 0.12em;
  }
  /* Front side */
  .card--front {
    left: 596px;
    width: 480px;
    height: 292px;
    background: linear-gradient(180deg, var(--paper) 0%, var(--paper) 55%, var(--paper-shade) 100%);
    color: var(--navy-ink);
  }
  .front-waves {
    position: absolute;
    top: 0; left: 0;
    width: 480px;
    height: 292px;
    fill: var(--wave);
  }
  .tagline {
    position: absolute;
    top: 20px;
    right: 35px;
    text-align: right;
    color: var(--white);
    font-size: 13.5px;
    line-height: 18px;
    letter-spacing: 0.06em;
  }
  .brand {
    position: absolute;
    left: 30px;
    top: 124px;
    font-weight: 500;
    color: var(--navy-ink);
  }
  .brand-name {
    font-size: 31px;
    letter-spacing: 0.42em;
    line-height: 1;
  }
  .brand-line {
    margin-top: 16px;
    margin-left: 19px;
    font-size: 12.5px;
    letter-spacing: 0.14em;
  }
  .person {
    position: absolute;
    left: 30px;
    top: 218px;
  }
  .person-name { font-size: 22px; line-height: 26px; font-weight: 500; }
  .person-role { font-size: 13.5px; line-height: 18px; }
  .contacts {
    position: absolute;
    right: 35px;
    top: 203px;
    list-style: none;
    text-align: right;
    font-size: 12px;
  }
  .contacts li {
    display: flex;
    justify-content: flex-end;
    align-items: center;
    gap: 8px;
    height: 20px;
  }
  .contacts svg { width: 11px; height: 11px; fill: var(--navy-ink); }
</style>
</head>
<body>

<section class="card card--back" aria-label="Card back">
  <div class="brand-name">ARVALE</div>
  <div class="brand-line">WEALTH PARTNERS</div>
</section>

<section class="card card--front" aria-label="Card front">
  <svg class="front-waves" viewBox="0 0 600 365" preserveAspectRatio="none" aria-hidden="true">
    <path d="M0 0 H600 V102 C500 118 420 80 330 40 C240 5 110 2 0 32 Z"/>
    <path d="M0 62 C110 30 240 28 320 58 C420 98 500 128 600 112 V140 C500 152 420 128 320 82 C240 48 120 42 0 72 Z"/>
  </svg>

  <p class="tagline">Clear Plans for<br>Every Tomorrow</p>

  <div class="brand">
    <div class="brand-name">ARVALE</div>
    <div class="brand-line">WEALTH PARTNERS</div>
  </div>

  <div class="person">
    <div class="person-name">Daniel Reyes</div>
    <div class="person-role">Managing Director</div>
  </div>

  <ul class="contacts">
    <li>555-014-2286
      <svg viewBox="0 0 24 24" aria-hidden="true"><path d="M3 9c0-4 18-4 18 0v2h-5V9H8v2H3z M6 12h12l2 8H4z"/></svg>
    </li>
    <li>daniel@arvalewealth.com
      <svg viewBox="0 0 24 24" aria-hidden="true"><path d="M2 5h20v14H2z M3 6l9 7 9-7" stroke="#f1f1f1" stroke-width="1.5"/></svg>
    </li>
    <li>www.arvalewealth.com
      <svg viewBox="0 0 24 24" aria-hidden="true"><circle cx="12" cy="12" r="10"/><path d="M2 12h20M12 2c-4 5-4 15 0 20M12 2c4 5 4 15 0 20" stroke="#f1f1f1" stroke-width="1.4" fill="none"/></svg>
    </li>
  </ul>
</section>

</body>
</html>
```